Tellmora Corporate Stationery

Look for design of all new corporate stationery for an existing insurance broking business that is going through a redesign and move from older partners to younger family members. New Logo is attached. Company is Brisbane based.
Colours in the Logo is Hex #43bed8 and website features a lot of hex #17b8d8. Website front page "A plan to protect you" - headline. "Professional and Individual advice to protect your greatest assets" - tagline.

Stationery required: Business Cards, Letter head, Thank-you cards, Birthday cards, Presentation folders, With Compliment slips and a powerpoint template. We also would like to send a card to all customers with the something along of the lines of "something new".

Target Market(s)

Customers of Insurance business looking at superannuation, life and income protection insurance, investment advice and wills

Industry/Entity Type

Insurance Broker

Font styles to use
Other font styles liked:
• same as logo

Requirements
Must have
• The above designs for new stationery for the new business including:
• Business Cards, Letter head, Thank-you cards, Birthday cards, Presentation folders, With Compliment slips and a powerpoint template. We also would like to send a card to all customers with the something along of the lines of "something new".
Nice to have
• It is a new look - long time family business being passed to next generation - big focus on advice for YOU, individual advice etc..

```html
<!DOCTYPE html>
<html lang="en">
<head>
<meta charset="utf-8">
<title>Tellmora Business Card</title>
<link href="https://fonts.googleapis.com/css2?family=Open+Sans:ital,wght@0,400;0,600;1,400&display=swap" rel="stylesheet">
<style>
  :root {
    --backdrop: #2b2b2c;
    --card-white: #ffffff;
    --card-grey: #808185;
    --brand-cyan: #3fbcd7;
    --text-grey: #5a5b5e;
    --rule-grey: #9a9b9e;
    --strip-grey: #6e6f73;
  }
  * { margin: 0; padding: 0; box-sizing: border-box; }
  html, body {
    width: 1200px; height: 987px; overflow: hidden;
    background: var(--backdrop);
    font-family: "Open Sans", Arial, sans-serif;
  }
  .stage { position: relative; width: 1200px; height: 987px; }

  .card { position: absolute; width: 615px; height: 352px; overflow: hidden; }
  .card-front { left: 293px; top: 130px; background: var(--card-white); }
  .card-back { left: 292px; top: 505px; background: var(--card-grey); }

  .brand { position: absolute; display: flex; align-items: center; gap: 12px; }
  .brand-name { font-weight: 600; letter-spacing: 0.5px; }
  .card-front .brand { right: 29px; top: 64px; }
  .card-front .brand-name { font-size: 40px; color: var(--brand-cyan); }
  .card-front .brand-dot { width: 40px; height: 40px; border-radius: 50%; background: var(--card-grey); }

  .person { position: absolute; left: 26px; top: 136px; }
  .person-name { font-size: 23px; font-weight: 600; color: var(--brand-cyan); line-height: 1.2; }
  .person-role { font-size: 17px; color: var(--text-grey); line-height: 1.3; }

  .divider { position: absolute; left: 26px; right: 29px; top: 216px; height: 1px; background: var(--rule-grey); }

  .contact-list { position: absolute; left: 26px; top: 222px; list-style: none; }
  .contact-list li {
    display: flex; align-items: center; gap: 8px;
    height: 23.5px; font-size: 16px; color: var(--text-grey);
  }
  .contact-list svg { width: 16px; height: 16px; fill: var(--brand-cyan); flex: none; }

  .address {
    position: absolute; right: 29px; top: 265px; text-align: right;
    font-size: 16px; line-height: 23px; color: var(--text-grey);
  }

  .footer-strip { position: absolute; left: 0; bottom: 0; width: 380px; height: 12px; background: var(--strip-grey); }
  .footer-band {
    position: absolute; right: 0; bottom: 0; width: 270px; height: 33px;
    background: var(--brand-cyan);
    clip-path: polygon(16px 0, 100% 0, 100% 100%, 0 100%);
    display: flex; align-items: center; justify-content: flex-end; padding-right: 26px;
    font-size: 15px; letter-spacing: 2.6px; color: var(--card-white);
  }

  .card-back .brand { right: 44px; top: 205px; }
  .card-back .brand-name { font-size: 34px; color: var(--card-white); }
  .card-back .brand-dot { width: 34px; height: 34px; border-radius: 50%; background: var(--card-white); }
  .back-web {
    position: absolute; right: 30px; top: 312px;
    font-size: 15px; font-style: italic; color: var(--card-white);
  }
</style>
</head>
<body>
<main class="stage">
  <section class="card card-front">
    <div class="brand">
      <span class="brand-dot"></span>
      <span class="brand-name">Tellmora</span>
    </div>

    <div class="person">
      <p class="person-name">Daniel Reeve</p>
      <p class="person-role">CEO/Founder</p>
    </div>
    <div class="divider"></div>

    <ul class="contact-list">
      <li>
        <svg viewBox="0 0 16 16" aria-hidden="true"><path d="M3.6 1.2l2.3 2.9-1.3 1.9c.9 2 2.6 3.7 4.6 4.6l1.9-1.3 2.9 2.3-1.4 2.6C6.9 14.6 1.4 9.1 1 2.6z"/></svg>
        614 207 3385
      </li>
      <li>
        <svg viewBox="0 0 16 16" aria-hidden="true"><path d="M4.5 0h7A1.5 1.5 0 0 1 13 1.5v13a1.5 1.5 0 0 1-1.5 1.5h-7A1.5 1.5 0 0 1 3 14.5v-13A1.5 1.5 0 0 1 4.5 0zM5 2v10h6V2zm3 11a1 1 0 1 0 0 2 1 1 0 0 0 0-2z"/></svg>
        742 519 6028
      </li>
      <li>
        <svg viewBox="0 0 16 16" aria-hidden="true"><path d="M4 1h8v4H4zM1 6h14v7h-2v-3H3v3H1zm3 5h8v4H4z"/></svg>
        358 661 4072
      </li>
      <li>
        <svg viewBox="0 0 16 16" aria-hidden="true"><path d="M1 3h14v10H1zm1.2 1.2L8 8.6l5.8-4.4z"/></svg>
        daniel@tellmora.com
      </li>
    </ul>

    <address class="address" style="font-style:normal">
      42 Wattle Grove Road<br>
      Larchmont, Oregon 52819
    </address>

    <div class="footer-strip"></div>
    <div class="footer-band">www.tellmora.com</div>
  </section>

  <section class="card card-back">
    <div class="brand">
      <span class="brand-dot"></span>
      <span class="brand-name">Tellmora</span>
    </div>
    <p class="back-web">www.tellmora.com</p>
  </section>
</main>
</body>
</html>
```